Vellmore Family Law, legal technician needs a website and design

I need a website for a family law practice. I specialize in collaborative law, unbundled services, and mediation. The website must contain my company logo (file attached), and the website must be a mixture of my personality and my profession. I have attached additional information to explain my personality and profession.

Target Market(s)

Lower through middle-class (income level up to $200,000 per year)

Coding

Coded - Design and coding required

Number of Pages Required

1 page

Requirements
Must have
• Must have enough pages to cover required content. I submitted below some content about the collaborative law process. All of the content is not necessary. However, the website must have enough content to clearly describe the services I offer. Use your professionalism and judgment regarding font, font size, etc.

```html
<!DOCTYPE html>
<html lang="en">
<head>
<meta charset="utf-8">
<title>Vellmore Family Law</title>
<link rel="stylesheet" href="https://fonts.googleapis.com/css2?family=Cinzel:wght@400;500&family=Lato:wght@400;700&display=swap">
<style>
:root{
  --gold:#b9b44a;
  --gold-title:#b1a33c;
  --gold-dark:#8a7d35;
  --gold-btn-a:#b0a545;
  --gold-btn-b:#7a7029;
  --ink:#1b1b1b;
  --muted:#8c8c8c;
  --panel:#efefef;
  --footer:#0f0f0f;
  --white:#ffffff;
}
*{margin:0;padding:0;box-sizing:border-box}
html,body{width:1200px;height:4329px;overflow:hidden;background:var(--white)}
body{position:relative;font-family:'Lato',sans-serif;color:var(--ink)}
.abs{position:absolute}
.serif{font-family:'Cinzel',serif}
.btn{position:absolute;display:flex;align-items:center;justify-content:center;font-size:15px;font-weight:700;color:var(--white);background:linear-gradient(180deg,var(--gold-btn-a),var(--gold-btn-b))}
.btn-light{background:var(--white);color:var(--gold-dark);font-weight:400}
.photo{position:absolute}

/* header */
.brand{left:97px;top:22px;display:flex;align-items:center;gap:14px}
.brand-mark{width:56px;height:56px;border:3px solid var(--gold-dark)}
.brand-name{font-family:'Cinzel',serif;font-size:24px;line-height:1.05;color:var(--gold-dark)}
.call{left:840px;top:18px;width:263px;height:37px;font-weight:400;font-size:15px}
.nav{top:76px;left:0;font-size:14px}
.nav a{position:absolute;color:var(--ink);text-decoration:none;white-space:nowrap}
.nav a.active{color:var(--gold-dark)}

/* hero */
.hero-panel{left:479px;top:197px;width:625px;height:506px;background:var(--panel)}
.hero-kicker{left:568px;top:302px;font-size:15px}
.hero-title{left:566px;top:330px;font-size:54px;line-height:1.04;color:var(--gold-title)}
.hero-text{left:566px;top:460px;width:470px;font-size:18px;line-height:1.3}
.arrow-btn{position:absolute;width:45px;height:50px;background:var(--gold);display:flex;align-items:center;justify-content:center}

/* headings */
.section-title{position:absolute;left:0;width:1200px;text-align:center;font-family:'Cinzel',serif;font-size:40px;letter-spacing:2px}

/* services grid */
.cell{position:absolute;width:311px;height:234px;background:var(--panel);text-align:center;padding:24px 14px 0}
.cell h3{font-size:18px;font-weight:700;margin:10px 0 10px}
.cell p{font-size:12.5px;line-height:1.75;color:var(--muted)}
.cell .more{display:block;margin-top:10px;font-size:13px;font-weight:700;color:var(--gold)}
.notch{position:absolute;width:0;height:0;border-left:10px solid transparent;border-right:10px solid transparent}

/* how it works */
.how-band{left:0;top:1434px;width:1200px;height:423px;background:linear-gradient(100deg,#3b2f27 0%,#6b5847 35%,#2b2521 60%,#5a4a3e 100%)}
.how-title{top:1526px;color:var(--white)}
.how-sub{left:0;top:1584px;width:1200px;text-align:center;font-size:12.5px;color:var(--white)}
.how-box{left:134px;top:1632px;width:932px;height:425px;background:var(--gold)}
.how-head{left:709px;top:1706px;width:300px;font-size:20px;font-weight:700;line-height:1.4;color:var(--white)}
.how-text{left:710px;top:1777px;width:308px;font-size:12.5px;line-height:1.6;color:var(--white);text-align:justify}

/* why / benefits */
.block-title{font-family:'Cinzel',serif;font-size:40px;letter-spacing:1px}
.block-text{font-size:13px;line-height:1.55;color:var(--muted);text-align:justify}
.accent{position:absolute;background:var(--gold)}
.badge{position:absolute;width:120px;height:120px;border-radius:50%;background:var(--gold-dark);border:4px solid var(--white);display:flex;align-items:center;justify-content:center}

/* articles */
.article-photo{position:absolute;width:299px;height:165px}
.article-card{position:absolute;width:285px;height:204px;background:var(--white);box-shadow:0 2px 12px rgba(0,0,0,.12);text-align:center;padding:22px 20px 0}
.article-card h4{font-size:17px;font-weight:700;margin-bottom:12px}
.article-card p{font-size:12.5px;line-height:1.6;color:var(--muted)}
.article-card .more{display:block;margin-top:14px;font-size:13.5px;font-weight:700;color:var(--gold-dark)}

/* call to action */
.cta{left:0;top:3766px;width:1200px;height:137px;background:linear-gradient(180deg,#b4a843 0%,#8e8430 100%)}
.cta-text{left:138px;top:3808px;width:620px;font-size:18px;font-weight:700;line-height:1.4;color:var(--white)}

/* footer */
.footer{left:0;top:3903px;width:1200px;height:426px;background:var(--footer)}
.foot-head{font-family:'Cinzel',serif;font-size:26px;color:var(--white);letter-spacing:1px}
.foot-links{left:649px;top:4088px;font-size:13px;line-height:22.7px;color:var(--white);list-style:none}
.contact-row{position:absolute;left:859px;display:flex;gap:12px;font-size:13px;line-height:22px;color:var(--white)}
.contact-row svg{margin-top:5px;flex:none}
.next{left:1118px;top:4003px;font-size:9px;color:#888}
.copy{left:0;top:4288px;width:1200px;text-align:center;font-size:10.5px;color:var(--white)}
</style>
</head>
<body>

<!-- header -->
<div class="abs brand">
  <div class="brand-mark"></div>
  <div class="brand-name">Vellmore<br>Family Law</div>
</div>
<div class="btn call">Call Us : + 888 8888 8888 8</div>
<nav class="abs nav">
  <a class="active" style="left:474px">Home</a>
  <a style="left:550px">About Us</a>
  <a style="left:645px">What We do</a>
  <a style="left:760px">How It Works</a>
  <a style="left:882px">Services</a>
  <a style="left:971px">Blog</a>
  <a style="left:1037px">Contact Us</a>
</nav>

<!-- hero -->
<div class="photo" role="img" aria-label="Row of dark leather-bound law books on a shelf" style="left:0;top:104px;width:709px;height:508px;background:linear-gradient(180deg,#8e8e8e 0%,#6d6d6d 18%,#1e2430 22%,#2a303b 60%,#0d0d0d 100%)"></div>
<div class="abs hero-panel"></div>
<div class="arrow-btn" style="left:434px;top:561px"><svg width="10" height="12" viewBox="0 0 10 12"><path d="M7 1 2 6l5 5" fill="none" stroke="#fff" stroke-width="1.6"/></svg></div>
<div class="arrow-btn" style="left:479px;top:654px"><svg width="10" height="12" viewBox="0 0 10 12"><path d="M3 1l5 5-5 5" fill="none" stroke="#fff" stroke-width="1.6"/></svg></div>
<div class="abs hero-kicker">A Legal Technician</div>
<h1 class="abs serif hero-title">VELLMORE<br>FAMILY LAW</h1>
<p class="abs hero-text">Lorem ipsum dolor sit amet, consectetur adipiscing elit, sed do eiusmod tempor incididunt ut labore aliquip ex ea commodo consequat.</p>
<div class="btn" style="left:566px;top:556px;width:168px;height:39px">Get Started</div>

<!-- services -->
<h2 class="section-title" style="top:796px">OUR SERVICES</h2>
<div class="photo" role="img" aria-label="Two businessmen shaking hands by a tall office window" style="left:134px;top:862px;width:311px;height:234px;background:linear-gradient(135deg,#c9d6e2,#7d90a3 55%,#3c4854)"></div>
<div class="cell" style="left:445px;top:862px">
  <svg width="52" height="46" viewBox="0 0 52 46"><rect x="8" y="4" width="36" height="34" fill="none" stroke="#a89a40" stroke-width="2"/><circle cx="26" cy="22" r="6" fill="none" stroke="#a89a40" stroke-width="2"/><path d="M12 10h10M12 30h8" stroke="#a89a40" stroke-width="2"/></svg>
  <h3>Unbundled Services</h3>
  <p>Lorem ipsum dolor sit amet, consectetur adipiscing elit, sed do eiusmod tempor incididunt ut labore et dolore magna aliqua.</p>
  <span class="more">READ MORE</span>
</div>
<div class="photo" role="img" aria-label="Legal team meeting around a laptop in a library" style="left:756px;top:862px;width:310px;height:234px;background:linear-gradient(135deg,#8a4a2a,#5b3828 45%,#d9cfc4)"></div>
<div class="notch" style="left:592px;top:1086px;border-bottom:10px solid var(--gold-dark)"></div>

<div class="cell" style="left:134px;top:1096px">
  <svg width="56" height="46" viewBox="0 0 56 46"><circle cx="28" cy="12" r="6" fill="none" stroke="#a89a40" stroke-width="2"/><path d="M6 12h14M36 12h14M6 40c0-8 6-10 10-10s10 2 10 10M30 40c0-8 6-10 10-10s10 2 10 10" fill="none" stroke="#a89a40" stroke-width="2"/></svg>
  <h3>Collaborative Law</h3>
  <p>Lorem ipsum dolor sit amet, consectetur adipiscing elit, sed do eiusmod tempor incididunt ut labore et dolore magna aliqua.</p>
  <span class="more">READ MORE</span>
</div>
<div class="notch" style="left:280px;top:1096px;border-top:10px solid var(--gold-dark)"></div>
<div class="photo" role="img" aria-label="Judge's gavel on a table beside a laptop and notebook" style="left:445px;top:1096px;width:311px;height:234px;background:linear-gradient(135deg,#6a4a34,#3b2d24 50%,#c8c2b8)"></div>
<div class="cell" style="left:756px;top:1096px">
  <svg width="52" height="46" viewBox="0 0 52 46"><rect x="12" y="2" width="28" height="18" fill="none" stroke="#a89a40" stroke-width="2"/><path d="M18 9h16M18 14h10" stroke="#a89a40" stroke-width="2"/><circle cx="14" cy="30" r="4" fill="none" stroke="#a89a40" stroke-width="2"/><circle cx="38" cy="30" r="4" fill="none" stroke="#a89a40" stroke-width="2"/><path d="M6 44c0-6 4-8 8-8s8 2 8 8M30 44c0-6 4-8 8-8s8 2 8 8" fill="none" stroke="#a89a40" stroke-width="2"/></svg>
  <h3>Mediation</h3>
  <p>Lorem ipsum dolor sit amet, consectetur adipiscing elit, sed do eiusmod tempor incididunt ut labore et dolore magna aliqua.</p>
  <span class="more">READ MORE</span>
</div>

<!-- how it works -->
<div class="abs how-band" role="img" aria-label="Close view of hands clasped across a desk during a consultation"></div>
<h2 class="section-title how-title">HOW IT WORKS</h2>
<p class="abs how-sub">Lorem ipsum dolor sit amet, consectetur adipiscing elit, sed do eiusmod tempor incididunt ut labore et dolore magna aliqua.</p>
<div class="abs how-box"></div>
<div class="photo" role="img" aria-label="Colleagues reviewing documents together around a wooden table" style="left:183px;top:1696px;width:498px;height:301px;background:linear-gradient(135deg,#d8d4cc,#b88a5a 45%,#3c3c44)"></div>
<h3 class="abs how-head">Lorem ipsum dolor sit amet, consectetur adipiscing</h3>
<p class="abs how-text">Lorem ipsum dolor sit amet, consectetur adipiscing elit, sed do eiusmod tempor incididunt ut labore et dolore magna aliqua. Ut enim ad minim veniam, quis nostrud exercitation ullamco laboris nisi ut aliquip ex ea commodo consequat. Duis aute irure dolor in reprehenderit in voluptate velit esse cillum dolore eu fugiat nulla pariatur.</p>
<div class="btn btn-light" style="left:711px;top:1945px;width:165px;height:37px">Contact Us</div>

<!-- why us -->
<h2 class="abs block-title" style="left:140px;top:2220px">WHY US</h2>
<p class="abs block-text" style="left:140px;top:2284px;width:307px">Lorem ipsum dolor sit amet, consectetur adipiscing elit, sed do eiusmod tempor incididunt ut labore et dolore magna aliqua. Ut enim ad minim veniam, quis nostrud exercitation ullamco laboris nisi ut aliquip ex ea commodo consequat. Duis aute irure dolor in reprehenderit in voluptate velit esse cillum dolore eu fugiat nulla pariatur.</p>
<div class="btn" style="left:140px;top:2455px;width:166px;height:38px">Read More</div>
<div class="accent" style="left:800px;top:2341px;width:301px;height:261px"></div>
<div class="photo" role="img" aria-label="Mother and daughter smiling while looking at a phone" style="left:597px;top:2160px;width:469px;height:403px;background:linear-gradient(135deg,#e9e4dc,#c9a48a 45%,#7a93b4)"></div>
<div class="badge" style="left:533px;top:2300px">
  <svg width="56" height="52" viewBox="0 0 56 52"><path d="M6 16 28 4l22 12z" fill="none" stroke="#fff" stroke-width="2.4"/><path d="M10 20v22M20 20v22M30 20v22M40 20v22M4 46h48" stroke="#fff" stroke-width="2.4"/></svg>
</div>

<!-- benefits -->
<div class="accent" style="left:97px;top:2887px;width:301px;height:259px"></div>
<div class="photo" role="img" aria-label="Man and woman reviewing paperwork at an office desk" style="left:136px;top:2703px;width:471px;height:403px;background:linear-gradient(135deg,#dcd8d0,#a8a49c 40%,#3a3e4a 70%,#7a2a30)"></div>
<div class="badge" style="left:542px;top:2844px">
  <svg width="56" height="52" viewBox="0 0 56 52"><circle cx="16" cy="10" r="4" fill="none" stroke="#fff" stroke-width="2.2"/><circle cx="28" cy="7" r="4" fill="none" stroke="#fff" stroke-width="2.2"/><circle cx="40" cy="10" r="4" fill="none" stroke="#fff" stroke-width="2.2"/><path d="M10 26c0-6 3-8 6-8M22 24c0-6 3-9 6-9s6 3 6 9M46 26c0-6-3-8-6-8M4 36l12 10h20l14-12" fill="none" stroke="#fff" stroke-width="2.2"/></svg>
</div>
<h2 class="abs block-title" style="left:758px;top:2766px">BENEFITS</h2>
<p class="abs block-text" style="left:756px;top:2830px;width:306px">Lorem ipsum dolor sit amet, consectetur adipiscing elit, sed do eiusmod tempor incididunt ut labore et dolore magna aliqua. Ut enim ad minim veniam, quis nostrud exercitation ullamco laboris nisi ut aliquip ex ea commodo consequat. Duis aute irure dolor in reprehenderit in voluptate velit esse cillum dolore eu fugiat nulla pariatur.</p>
<div class="btn" style="left:756px;top:3000px;width:165px;height:37px">Read More</div>

<!-- articles -->
<h2 class="section-title" style="top:3240px">ARTICLES</h2>
<div class="article-photo" role="img" aria-label="Hands signing a document with a pen" style="left:140px;top:3311px;background:linear-gradient(135deg,#5a4a3c,#c8bfb2 60%,#8a7a68)"></div>
<div class="article-photo" role="img" aria-label="Team working on laptops at a white desk seen from above" style="left:452px;top:3311px;background:linear-gradient(135deg,#f0f0f0,#9aa6b4 50%,#2e3440)"></div>
<div class="article-photo" role="img" aria-label="Stone steps and columns of a courthouse" style="left:765px;top:3311px;background:linear-gradient(180deg,#b8b8b8,#8a8a8a 50%,#d4d4d4)"></div>
<div class="article-card" style="left:147px;top:3460px"><h4>Lorem ipsum dolor</h4><p>Lorem ipsum dolor sit amet, consectetur adipiscing elit, sed do eiusmod tempor incididunt ut labore et dolore magna aliqua.</p><span class="more">Read More</span></div>
<div class="article-card" style="left:459px;top:3460px"><h4>Lorem ipsum dolor</h4><p>Lorem ipsum dolor sit amet, consectetur adipiscing elit, sed do eiusmod tempor incididunt ut labore et dolore magna aliqua.</p><span class="more">Read More</span></div>
<div class="article-card" style="left:772px;top:3460px"><h4>Lorem ipsum dolor</h4><p>Lorem ipsum dolor sit amet, consectetur adipiscing elit, sed do eiusmod tempor incididunt ut labore et dolore magna aliqua.</p><span class="more">Read More</span></div>

<!-- call to action -->
<div class="abs cta"></div>
<p class="abs cta-text">Lorem ipsum dolor sit amet, consectetur adipiscing elit, sed do eiusmod tempor incididunt ut labore et dolore magna aliqua.</p>
<div class="btn btn-light" style="left:899px;top:3817px;width:165px;height:37px">Contact Us</div>

<!-- footer -->
<div class="abs footer"></div>
<div class="abs brand" style="left:138px;top:3990px">
  <div class="brand-mark"></div>
  <div class="brand-name">Vellmore<br>Family Law</div>
</div>
<h3 class="abs foot-head" style="left:649px;top:3994px">LINKS</h3>
<ul class="abs foot-links">
  <li>Home</li><li>About Us</li><li>What We do</li><li>How It Works</li><li>Services</li><li>Blog</li><li>Contact Us</li>
</ul>
<h3 class="abs foot-head" style="left:857px;top:3994px">CONTACT US</h3>
<div class="contact-row" style="top:4052px">
  <svg width="10" height="13" viewBox="0 0 10 13"><path d="M5 12S1 7 1 4.5a4 4 0 0 1 8 0C9 7 5 12 5 12z" fill="#fff"/><circle cx="5" cy="4.5" r="1.5" fill="#0f0f0f"/></svg>
  <span>Vellmore Family Law<br>Harlow County, Westbrook state</span>
</div>
<div class="contact-row" style="top:4118px">
  <svg width="12" height="12" viewBox="0 0 12 12"><path d="M2 1l2 .3 1 2.7-1.4 1a7 7 0 0 0 3.4 3.4l1-1.4 2.7 1L11 10c0 .6-.6 1-1 1A9 9 0 0 1 1 2c0-.4.4-1 1-1z" fill="#fff"/></svg>
  <span>+8 888 888 888</span>
</div>
<div class="contact-row" style="top:4163px">
  <svg width="13" height="10" viewBox="0 0 13 10"><rect width="13" height="10" fill="#fff"/><path d="M0 0l6.5 5L13 0" fill="none" stroke="#0f0f0f" stroke-width="1.2"/></svg>
  <span>info@vellmorelaw.com</span>
</div>
<div class="abs next">NEXT STEP »</div>
<p class="abs copy">Copyright © 2021 The Company Name &nbsp;|&nbsp; Terms of Use Privacy Policy</p>

</body>
</html>
```